Law Firm Header Revision

Task: Redesign my law firm Word document header (modern, succinct, logo-first, easy address updates)

I need you to revise and modernize my Microsoft Word document header for Law Office of Bram Holcott, PLLC. The result should look professional and clean on letters (including Letters of Protection), with the logo as the main focus and the text kept succinct.

Goals:
1. Create a modern, minimal header that feels premium and uncluttered.
Make the logo the most visually dominant element.
Reduce the visual weight of the contact/address block so it doesn’t distract from the document.
Make the address easy to change later (I’m moving offices soon) while keeping the same header design.

2. Content to include (keep all info accurate):
Law Office of Bram Holcott, PLLC
615 Pemberly St. Ste #300-214, Houston, TX 77002
Office: 832.555.0143
Direct: 713.555.0187
Fax: 832.555.0129
Bholcottlaw.com

3. Layout requirements:
Provide 3 header style options:
Logo left + contact info right
Centered logo + single concise contact line below
Logo left + firm name prominent + minimal contact line
The primary line near the logo should be minimal (preferably website + main office phone).
The address should be easy to update in one place without redesigning the header. Prefer either:
Move the full address to the footer, or
Put the address in a single dedicated line/block so I can edit it once and keep the layout unchanged.
4. Build constraints:
Must be achievable using standard Microsoft Word tools only (header/footer, tables, alignment, fonts, spacing). No advanced graphics software.
Provide exact header text, plus step-by-step Word instructions for each option:
Font recommendations + sizes
Alignment
Spacing
Table setup (if used)
How to keep it consistent across pages

5. Deliverable:
For each of the 3 options, provide:
The exact header content (with line breaks)
Formatting specs (fonts, sizes, spacing)
Word build steps so I can recreate it reliably and keep the logo as the focal point.

```html
<!DOCTYPE html>
<html lang="en">
<head>
<meta charset="utf-8">
<title>Bram Holcott Law – Letterhead Options</title>
<link href="https://fonts.googleapis.com/css2?family=Montserrat:wght@400;500;600;700&display=swap" rel="stylesheet">
<style>
  :root {
    --backdrop: #6f8fae;
    --navy: #0c1f33;
    --paper: #ffffff;
    --footer-tint: #e8ecf0;
    --ink: #0c1f33;
  }
  html, body {
    margin: 0;
    padding: 0;
    width: 1200px;
    height: 525px;
    overflow: hidden;
    background: var(--backdrop);
    font-family: "Montserrat", Arial, sans-serif;
  }
  .sheet-row { position: relative; width: 1200px; height: 525px; }
  .sheet { position: absolute; top: 15px; width: 382px; height: 495px; background: var(--paper); }
  .sheet--logo-right { left: 14px; }
  .sheet--centered { left: 408px; }
  .sheet--firm-name { left: 802px; }
  .sheet svg { display: block; width: 382px; height: 495px; }
  .icon-lib { position: absolute; width: 0; height: 0; }

  .navy-fill { fill: var(--navy); }
  .tint-fill { fill: var(--footer-tint); }
  .rule { stroke: var(--navy); stroke-width: 0.8; }
  .wordmark { font-family: "Montserrat", Arial, sans-serif; font-weight: 600; font-size: 12.5px; fill: var(--ink); letter-spacing: 0.4px; }
  .band-text { font-size: 5.8px; font-weight: 400; fill: #ffffff; letter-spacing: 0.15px; }
  .band-firm { font-size: 6.3px; font-weight: 600; fill: #ffffff; }
  .contact-line { font-size: 5.2px; font-weight: 400; fill: var(--ink); }
  .footer-firm { font-size: 6.6px; font-weight: 600; fill: var(--ink); }
  .footer-detail { font-size: 4.9px; font-weight: 400; fill: var(--ink); }
  .footer-label { font-size: 4.2px; font-weight: 700; fill: var(--ink); letter-spacing: 0.1px; }
  .page-tag { font-size: 4.2px; font-weight: 700; fill: #ffffff; }
</style>
</head>
<body>

<svg class="icon-lib" aria-hidden="true">
  <defs>
    <symbol id="icon-building" viewBox="0 0 10 10">
      <rect x="2" y="0.5" width="6" height="9" fill="currentColor"/>
      <rect x="3.2" y="1.8" width="1.2" height="1.2" fill="var(--navy)"/>
      <rect x="5.6" y="1.8" width="1.2" height="1.2" fill="var(--navy)"/>
      <rect x="3.2" y="4.2" width="1.2" height="1.2" fill="var(--navy)"/>
      <rect x="5.6" y="4.2" width="1.2" height="1.2" fill="var(--navy)"/>
    </symbol>
    <symbol id="icon-globe" viewBox="0 0 10 10">
      <circle cx="5" cy="5" r="4.2" fill="none" stroke="currentColor" stroke-width="1"/>
      <ellipse cx="5" cy="5" rx="1.8" ry="4.2" fill="none" stroke="currentColor" stroke-width="0.8"/>
      <line x1="0.8" y1="5" x2="9.2" y2="5" stroke="currentColor" stroke-width="0.8"/>
    </symbol>
    <symbol id="icon-pin" viewBox="0 0 10 10">
      <path d="M5 0.5a3.3 3.3 0 0 1 3.3 3.3C8.3 6.3 5 9.5 5 9.5S1.7 6.3 1.7 3.8A3.3 3.3 0 0 1 5 0.5z" fill="currentColor"/>
      <circle cx="5" cy="3.8" r="1.2" fill="#e8ecf0"/>
    </symbol>
    <symbol id="icon-phone" viewBox="0 0 10 10">
      <path d="M2 0.8l1.8 0 0.8 2.4-1.2 0.9a6 6 0 0 0 2.5 2.5l0.9-1.2 2.4 0.8 0 1.8a1.2 1.2 0 0 1-1.3 1.1C4 8.8 1.2 6 0.9 2.1A1.2 1.2 0 0 1 2 0.8z" fill="currentColor"/>
    </symbol>
    <symbol id="icon-fax" viewBox="0 0 10 10">
      <rect x="0.8" y="3" width="8.4" height="6" fill="currentColor"/>
      <rect x="2.5" y="0.8" width="5" height="2.8" fill="currentColor"/>
      <rect x="2.5" y="5" width="5" height="0.8" fill="#e8ecf0"/>
      <rect x="2.5" y="6.6" width="5" height="0.8" fill="#e8ecf0"/>
    </symbol>
  </defs>
</svg>

<main class="sheet-row">

  <!-- Option 1: logo left + contact right -->
  <section class="sheet sheet--logo-right" aria-label="Option 1: logo left, contact right">
    <svg viewBox="0 0 382 495">
      <g class="brand">
        <rect class="navy-fill" x="12" y="12" width="28" height="30"/>
        <text class="wordmark" x="46" y="32">BRAM HOLCOTT</text>
      </g>
      <g class="header-band">
        <line class="rule" x1="218" y1="15" x2="310" y2="15"/>
        <polygon class="navy-fill" points="218,17 382,17 382,32 228,32"/>
        <line class="rule" x1="228" y1="34" x2="382" y2="34"/>
        <use href="#icon-building" x="243" y="21.5" width="6" height="6" style="color:#fff"/>
        <text class="band-text" x="252" y="26.6">713.555.0187 (Office)</text>
        <use href="#icon-globe" x="318" y="21.5" width="6" height="6" style="color:#fff"/>
        <text class="band-text" x="327" y="26.6">Bholcottlaw.com</text>
      </g>
      <g class="letter-footer">
        <rect class="navy-fill" x="0" y="450" width="382" height="2"/>
        <rect class="tint-fill" x="0" y="452" width="382" height="43"/>
        <text class="footer-label" x="10" y="476">LETTER OF PROTECTION</text>
        <text class="footer-firm" x="191" y="465.5" text-anchor="middle">Law Office of Bram Holcott, PLLC</text>
        <use href="#icon-pin" x="127" y="471" width="4.6" height="4.6" style="color:var(--navy)"/>
        <text class="footer-detail" x="134" y="475.2">615 Pemberly St. Ste #300-214, Houston, TX 77002</text>
        <use href="#icon-phone" x="144" y="481" width="4.4" height="4.4" style="color:var(--navy)"/>
        <text class="footer-detail" x="151" y="485">713.555.0187   |</text>
        <use href="#icon-fax" x="197" y="481" width="4.4" height="4.4" style="color:var(--navy)"/>
        <text class="footer-detail" x="204" y="485">832.555.0129</text>
        <polygon class="navy-fill" points="332,463 382,463 382,486 343,486"/>
        <text class="page-tag" x="363" y="476">PAGE 1</text>
      </g>
    </svg>
  </section>

  <!-- Option 2: centered logo + single contact line -->
  <section class="sheet sheet--centered" aria-label="Option 2: centered logo with contact line">
    <svg viewBox="0 0 382 495">
      <g class="brand">
        <rect class="navy-fill" x="121" y="9" width="28" height="30"/>
        <text class="wordmark" x="155" y="29">BRAM HOLCOTT</text>
      </g>
      <g class="header-band">
        <line class="rule" x1="35" y1="46" x2="126" y2="46"/>
        <polygon class="navy-fill" points="0,47.5 127,47.5 117,58 0,58"/>
        <line class="rule" x1="257" y1="46" x2="349" y2="46"/>
        <polygon class="navy-fill" points="257,47.5 382,47.5 382,58 266,58"/>
        <use href="#icon-building" x="136" y="50" width="5" height="5" style="color:var(--navy)"/>
        <text class="contact-line" x="147" y="54.6">832.555.0143  |</text>
        <use href="#icon-globe" x="191" y="50" width="5" height="5" style="color:var(--navy)"/>
        <text class="contact-line" x="200" y="54.6">Bholcottlaw.com</text>
      </g>
      <g class="letter-footer">
        <rect class="navy-fill" x="0" y="450" width="382" height="2"/>
        <rect class="tint-fill" x="0" y="452" width="382" height="43"/>
        <text class="footer-label" x="10" y="476">LETTER OF PROTECTION</text>
        <text class="footer-firm" x="191" y="465.5" text-anchor="middle">Law Office of Bram Holcott, PLLC</text>
        <use href="#icon-pin" x="127" y="471" width="4.6" height="4.6" style="color:var(--navy)"/>
        <text class="footer-detail" x="134" y="475.2">615 Pemberly St. Ste #300-214, Houston, TX 77002</text>
        <use href="#icon-phone" x="144" y="481" width="4.4" height="4.4" style="color:var(--navy)"/>
        <text class="footer-detail" x="151" y="485">713.555.0187   |</text>
        <use href="#icon-fax" x="197" y="481" width="4.4" height="4.4" style="color:var(--navy)"/>
        <text class="footer-detail" x="204" y="485">832.555.0129</text>
        <polygon class="navy-fill" points="332,463 382,463 382,486 343,486"/>
        <text class="page-tag" x="363" y="476">PAGE 1</text>
      </g>
    </svg>
  </section>

  <!-- Option 3: logo left + firm name prominent -->
  <section class="sheet sheet--firm-name" aria-label="Option 3: logo left with firm name band">
    <svg viewBox="0 0 382 495">
      <g class="brand">
        <rect class="navy-fill" x="12" y="12" width="28" height="30"/>
        <text class="wordmark" x="45" y="32" style="font-size:12px">BRAM HOLCOTT</text>
      </g>
      <g class="header-band">
        <line class="rule" x1="150" y1="13" x2="268" y2="13"/>
        <polygon class="navy-fill" points="150,14.5 382,14.5 382,34 162,34"/>
        <line class="rule" x1="162" y1="36" x2="382" y2="36"/>
        <text class="band-firm" x="169" y="26.5">Law Office of Bram Holcott, PLLC</text>
        <use href="#icon-building" x="302" y="17.5" width="5.2" height="5.2" style="color:#fff"/>
        <text class="band-text" x="310" y="22" style="font-size:5.5px">713.555.0187 (Office)</text>
        <use href="#icon-globe" x="302" y="25.3" width="5.2" height="5.2" style="color:#fff"/>
        <text class="band-text" x="310" y="29.8" style="font-size:5.5px">Bholcottlaw.com</text>
      </g>
      <g class="letter-footer">
        <rect class="navy-fill" x="0" y="450" width="382" height="2"/>
        <rect class="tint-fill" x="0" y="452" width="382" height="43"/>
        <text class="footer-label" x="10" y="476">LETTER OF PROTECTION</text>
        <text class="footer-firm" x="191" y="465.5" text-anchor="middle">Law Office of Bram Holcott, PLLC</text>
        <use href="#icon-pin" x="127" y="471" width="4.6" height="4.6" style="color:var(--navy)"/>
        <text class="footer-detail" x="134" y="475.2">615 Pemberly St. Ste #300-214, Houston, TX 77002</text>
        <use href="#icon-phone" x="144" y="481" width="4.4" height="4.4" style="color:var(--navy)"/>
        <text class="footer-detail" x="151" y="485">713.555.0187   |</text>
        <use href="#icon-fax" x="197" y="481" width="4.4" height="4.4" style="color:var(--navy)"/>
        <text class="footer-detail" x="204" y="485">832.555.0129</text>
        <polygon class="navy-fill" points="332,463 382,463 382,486 343,486"/>
        <text class="page-tag" x="363" y="476">PAGE 1</text>
      </g>
    </svg>
  </section>

</main>
</body>
</html>
```